Business Card Design for Flood Rescue 360 - Property Restoration Professionals

I need a business card designed for Flood Rescue 360. We are a full-service property restoration solution. Providing water, fire, smoke & storm restoration as well as mold remediation and full remodel or reconstruction to homes and businesses across Dallas-Fort Worth, TX.
Target Market(s)
home and business owners with insurance covered property damage from water, fire or storm related damage
Industry/Entity Type
property restoration
Contact Information for Business Card
Marcus Pelley General Manager Cell: 214-555-0193 Office: 469-555-0148 email: Marcus@FloodRescue360.example services: Water, Fire, Mold, Reconstruction Tagline: Urgency for Your Water Emergency!
Look and feel
Each slider illustrates characteristics of the customer's brand and the style your logo design should communicate.

```html
<!DOCTYPE html>
<html lang="en">
<head>
<meta charset="utf-8">
<title>Flood Rescue 360 – Business Card</title>
<link href="https://fonts.googleapis.com/css2?family=Montserrat:wght@400;500;800&display=swap" rel="stylesheet">
<style>
  :root {
    --backdrop: #4a4a4a;
    --card: #121212;
    --cyan: #00b3ec;
    --white: #f2f2f2;
    --grey: #8a8a8a;
  }
  * { box-sizing: border-box; margin: 0; padding: 0; }
  html, body { width: 1200px; height: 801px; overflow: hidden; }
  body {
    background: var(--backdrop);
    font-family: "Montserrat", sans-serif;
    position: relative;
  }
  .card {
    position: absolute;
    top: 246px;
    width: 540px;
    height: 309px;
    background: var(--card);
    border-bottom: 4px solid var(--cyan);
    border-left: 2px solid var(--cyan);
    box-shadow: 0 14px 30px rgba(0,0,0,.45);
    overflow: hidden;
  }
  .card--front { left: 40px; }
  .card--back { left: 620px; }

  .brand {
    position: absolute;
    top: 34px;
    right: 32px;
    display: flex;
    align-items: center;
    gap: 12px;
  }
  .brand__name {
    color: var(--cyan);
    font-weight: 800;
    font-size: 30px;
    line-height: 1;
    text-transform: uppercase;
    text-align: right;
    width: 210px;
  }
  .brand__dot {
    width: 40px; height: 40px;
    border-radius: 50%;
    background: var(--cyan);
    flex: none;
  }

  .services {
    position: absolute;
    right: 32px;
    top: 130px;
    text-align: right;
  }
  .services__title {
    color: var(--cyan);
    font-weight: 800;
    font-size: 20px;
    letter-spacing: .5px;
    margin-bottom: 6px;
  }
  .services__item {
    color: var(--white);
    font-size: 13px;
    line-height: 1.55;
    display: flex;
    justify-content: flex-end;
    align-items: center;
    gap: 6px;
  }
  .services__item::after {
    content: "";
    width: 7px; height: 7px;
    border-radius: 50%;
    border: 1.5px solid var(--cyan);
  }

  .person {
    position: absolute;
    left: 30px;
    top: 118px;
  }
  .person__name {
    color: var(--cyan);
    font-weight: 800;
    font-size: 26px;
    line-height: 1.05;
  }
  .person__role {
    color: var(--white);
    font-size: 14px;
    margin-top: 4px;
  }
  .person__tagline {
    color: var(--white);
    font-size: 14px;
    margin-top: 14px;
  }
  .contacts {
    list-style: none;
    margin-top: 14px;
  }
  .contacts li {
    color: var(--white);
    font-size: 14px;
    line-height: 1.45;
    display: flex;
    align-items: center;
    gap: 8px;
  }
  .contacts svg { width: 13px; height: 13px; flex: none; }

  .pattern {
    position: absolute;
    inset: 0;
    background: radial-gradient(ellipse at 15% 70%, #3a3a3a 0%, #1c1c1c 45%, #0e0e0e 100%);
  }
  .back-brand {
    position: absolute;
    right: 70px;
    top: 150px;
    color: var(--cyan);
    font-weight: 800;
    font-size: 14px;
    text-transform: uppercase;
    background: var(--card);
    padding: 6px 10px;
  }
</style>
</head>
<body>

<section class="card card--front">
  <div class="brand">
    <div class="brand__name">Flood Rescue 360</div>
    <div class="brand__dot"></div>
  </div>

  <div class="services">
    <div class="services__title">SERVICES</div>
    <div class="services__item">Water</div>
    <div class="services__item">Fire</div>
    <div class="services__item">Mold</div>
    <div class="services__item">Reconstruction</div>
  </div>

  <div class="person">
    <div class="person__name">Marcus Pelley</div>
    <div class="person__role">General Manager</div>
    <div class="person__tagline">Urgency for Your Water Emergency!</div>
    <ul class="contacts">
      <li>
        <svg viewBox="0 0 14 14"><rect x="3.5" y="1" width="7" height="12" rx="1.2" fill="none" stroke="#00b3ec" stroke-width="1.5"/></svg>
        214-555-0193
      </li>
      <li>
        <svg viewBox="0 0 14 14"><path d="M1 5c0-2 3-3 6-3s6 1 6 3l-2 1-1-2H4L3 6z M3 8h8v5H3z" fill="#00b3ec"/></svg>
        469-555-0148
      </li>
      <li>
        <svg viewBox="0 0 14 14"><rect x="1" y="3" width="12" height="8" fill="none" stroke="#00b3ec" stroke-width="1.5"/><path d="M1 3l6 5 6-5" fill="none" stroke="#00b3ec" stroke-width="1.5"/></svg>
        Marcus@FloodRescue360.example
      </li>
      <li>
        <svg viewBox="0 0 14 14"><circle cx="7" cy="7" r="6" fill="#00b3ec"/><path d="M1 7h12M7 1c-3 3-3 9 0 12M7 1c3 3 3 9 0 12" fill="none" stroke="#121212" stroke-width="1"/></svg>
        FloodRescue360.example
      </li>
    </ul>
  </div>
</section>

<section class="card card--back">
  <div class="pattern" role="img" aria-label="Repeating pattern of the company mark in gloss black and silver"></div>
  <div class="back-brand">Flood Rescue 360</div>
</section>

</body>
</html>
```